Pelican HVAC WordPress website design

Design a new modern, clean, website for HVAC mechanical business that uses company logo/colors for branding and recognition. Files attached are just for band and color information. Here is a website design that appeals to me https://www.corvellsupply.example/

A clear description of who we are and what we do

An easily-navigated site map

An easily-navigated site map for mobile devices

Easy-to-find contact information

Obvious call to action for service, installs or to schedule estimates

about us page

Provide a way for potential customers to contact us via text or email

provide a way that allows a customer to upload a picture to request a service call or quote.
Updates

I'm looking for the design to be completed in WordPress

Industry/Entity Type

HVAC Mechanical & Building Automation / Controls contractor

Coding

Coded - Design and coding required

Number of Pages Required

5+ page

Colors
0054AA
0677BA
7BADD7
CADEEF
E8F1F8

Requirements
Must have
• Design a new modern, clean, website for HVAC mechanical business that uses company logo/colors for branding and recognition. Files attached are just for band and color information. Here is a website design that appeals to me https://www.corvellsupply.example/ A clear description of who we are and what we do An easily-navigated site map An easily-navigated site map for mobile devices Easy-to-find contact information Obvious call to action for service, installs or to schedule estimates about us page Provide a way for potential customers to contact us via text or email provide a way that allows a customer to upload a picture to request a service call or quote.
Nice to have

```html
<!DOCTYPE html>
<html lang="en">
<head>
<meta charset="utf-8">
<title>Pelican HVAC – Heating, Cooling &amp; Repairs</title>
<link rel="stylesheet" href="https://fonts.googleapis.com/css2?family=Roboto+Slab:wght@400;600;700&family=Roboto:ital,wght@0,400;0,500;0,700;0,900;1,400;1,500&display=swap">
<style>
:root{
  --navy:#123f7a;
  --navy-deep:#0c2f5e;
  --blue:#0054aa;
  --sky:#7badd7;
  --mist:#cadeef;
  --ice:#e8f1f8;
  --grey:#c4cad2;
  --grey-light:#dfe3e8;
  --ink:#1d2733;
  --text:#6b7280;
  --white:#ffffff;
  --black:#0b0b0c;
  --gold:#f2c230;
}
*{box-sizing:border-box;margin:0;padding:0}
html,body{width:1200px;height:5372px;overflow:hidden;background:var(--white)}
body{font-family:"Roboto",Arial,sans-serif;color:var(--ink)}
.page{position:relative;width:1200px;height:5372px;overflow:hidden}
.abs{position:absolute}
.slab{font-family:"Roboto Slab",Georgia,serif}
.btn{position:absolute;display:flex;align-items:center;justify-content:center;border:2px solid var(--navy);border-radius:30px;font:700 12px "Roboto",Arial,sans-serif;text-transform:uppercase;letter-spacing:.3px;color:var(--navy);background:var(--white)}
.btn.on-dark{border-color:var(--white);color:var(--white);background:transparent}
.photo{position:absolute;border-radius:50%;border:7px solid var(--white)}
.para{position:absolute;font-size:13px;line-height:23.5px;color:var(--text);text-align:justify}
.vertical{position:absolute;font:700 64px "Roboto Slab",Georgia,serif;color:rgba(18,63,122,.09);transform:rotate(-90deg);transform-origin:left top;letter-spacing:3px;white-space:nowrap}
.ghost{position:absolute;left:0;width:1200px;text-align:center;font:700 60px "Roboto Slab",Georgia,serif;text-transform:uppercase;letter-spacing:2px}
.h2{position:absolute;left:0;width:1200px;text-align:center;font:600 40px "Roboto Slab",Georgia,serif}

/* header */
.header{position:absolute;left:0;top:0;width:1200px;height:119px;background:var(--white)}
.nav a{position:absolute;top:82px;font:700 11.5px "Roboto",Arial,sans-serif;text-transform:uppercase;color:var(--navy-deep);text-decoration:none}
.nav .active{border:1.5px solid var(--navy);border-radius:20px;padding:6px 14px;top:76px}
.service-tab{position:absolute;left:745px;top:0;width:299px;height:69px;background:var(--navy);border-radius:0 0 50px 50px;color:var(--white)}
.brand{position:absolute;display:flex;align-items:center;gap:10px;font:700 30px "Roboto Slab",Georgia,serif;color:var(--navy)}
.brand i{display:block;width:22px;height:22px;border-radius:50%;background:var(--navy)}

/* hero */
.hero-title{position:absolute;left:144px;top:284px;font:700 49px/56px "Roboto Slab",Georgia,serif;color:var(--white);text-transform:uppercase}
.hero-sub{position:absolute;left:144px;top:416px;font:700 22px "Roboto Slab",Georgia,serif;color:var(--white);text-transform:uppercase;word-spacing:4px}

/* services */
.svc{position:absolute;width:208px;height:208px;border:2px solid var(--white);border-radius:50%;text-align:center;color:var(--white)}
.svc span{position:absolute;left:0;width:100%;top:132px;font:700 15px "Roboto",Arial,sans-serif}
.svc svg{position:absolute;left:74px;top:36px}
.arrow{position:absolute;width:46px;height:46px;border:2px solid var(--white);border-radius:50%}
.arrow svg{position:absolute;left:12px;top:12px}

/* areas */
.area-photo{position:absolute;top:2632px;width:219px;height:240px}
.area-label{position:absolute;top:2888px;width:219px;text-align:center;font:700 15px "Roboto",Arial,sans-serif;color:var(--ink);text-transform:uppercase}

/* news */
.card{position:absolute;top:3648px;width:295px;height:426px;border:2px solid var(--sky);background:var(--white)}
.card .img{height:223px;width:100%}
.card h3{margin:18px 22px 0;font:700 15.5px/22px "Roboto",Arial,sans-serif;color:var(--ink)}
.card p{margin:8px 22px 0;font-size:12.5px;line-height:22px;color:var(--text)}
.card .meta{margin:10px 22px 0;font:italic 500 12px "Roboto",Arial,sans-serif;color:var(--navy)}

/* form */
.field{position:absolute;height:46px;border:1.5px solid var(--navy);border-radius:30px;background:var(--white);font-size:11.5px;color:#6b7280;padding:14px 30px}
.radio{display:inline-block;width:14px;height:14px;border:1.5px solid #8a8f96;border-radius:50%;vertical-align:middle;margin:0 6px 0 18px}

/* footer */
.foot-h{position:absolute;top:5020px;font:500 17px "Roboto",Arial,sans-serif;color:var(--white);text-transform:uppercase}
.foot-t{position:absolute;font-size:12.5px;line-height:22px;color:#e5e7eb}
.quick a{display:block;font-size:12.5px;line-height:27px;color:#e5e7eb;text-decoration:none}
</style>
</head>
<body>
<div class="page">

  <!-- HEADER -->
  <header class="header">
    <div class="btn" style="left:146px;top:14px;width:240px;height:42px;font-size:11.5px">Schedule an appointment</div>
    <nav class="nav">
      <a class="active" style="left:174px">Home</a>
      <a style="left:264px">Who we are</a>
      <a style="left:382px">What we do</a>
      <a style="left:812px">News</a>
      <a style="left:887px">Contact us</a>
    </nav>
    <svg class="abs" style="left:1000px;top:82px" width="16" height="16" viewBox="0 0 16 16"><circle cx="6.5" cy="6.5" r="5" fill="none" stroke="#123f7a" stroke-width="2.4"/><line x1="10.3" y1="10.3" x2="15" y2="15" stroke="#123f7a" stroke-width="2.6" stroke-linecap="round"/></svg>
    <div class="service-tab">
      <svg class="abs" style="left:56px;top:14px" width="30" height="30" viewBox="0 0 30 30"><circle cx="15" cy="15" r="14" fill="#fff"/><path d="M10.5 8.5l3 3-1.6 2c1 2 2.6 3.6 4.6 4.6l2-1.6 3 3-2 2.2c-5.2-.4-10.8-6-11.2-11.2z" fill="#123f7a"/></svg>
      <div class="abs" style="left:97px;top:9px;font:700 11px Roboto,Arial,sans-serif;text-transform:uppercase">Request a service call</div>
      <div class="abs" style="left:97px;top:23px;font:700 21px Roboto,Arial,sans-serif">603-555-0148</div>
    </div>
  </header>

  <!-- HERO -->
  <svg class="abs" style="left:0;top:119px" width="1200" height="640" viewBox="0 119 1200 640">
    <defs>
      <linearGradient id="cityNight" x1="0" y1="0" x2="0" y2="1">
        <stop offset="0" stop-color="#16375e"/>
        <stop offset=".45" stop-color="#1f3147"/>
        <stop offset=".75" stop-color="#3a3327"/>
        <stop offset="1" stop-color="#1a2330"/>
      </linearGradient>
    </defs>
    <path d="M0 119H1200V540Q600 980 0 540Z" fill="#b9bec6"/>
    <path d="M0 119H1200V520Q600 930 0 520Z" fill="url(#cityNight)" role="img" aria-label="Night view of a New Hampshire city skyline lit up along the river"/>
  </svg>
  <h1 class="hero-title">Proud to serve New<br>Hampshire Communities</h1>
  <div class="hero-sub">Heating &nbsp;•&nbsp; Cooling &nbsp;•&nbsp; Repairs</div>
  <div class="btn" style="left:144px;top:473px;width:238px;height:40px;font-size:11.5px;border-color:#fff">Schedule an appointment</div>
  <svg class="abs" style="left:570px;top:630px" width="60" height="20"><circle cx="10" cy="10" r="4.5" fill="#fff"/><circle cx="30" cy="10" r="6.5" fill="none" stroke="#fff" stroke-width="2"/><circle cx="50" cy="10" r="4.5" fill="#fff"/></svg>

  <!-- WHO WE ARE -->
  <div class="abs" role="img" aria-label="Faint background of rooftop air conditioning units" style="left:0;top:740px;width:1200px;height:600px;background:linear-gradient(90deg,rgba(202,222,239,.45),rgba(255,255,255,0) 60%)"></div>
  <div class="vertical" style="left:1106px;top:985px">ABOUT</div>
  <div class="photo" role="img" aria-label="HVAC technician in a hard hat servicing rooftop units at sunset" style="left:116px;top:808px;width:416px;height:250px;background:linear-gradient(160deg,#e3a768,#6d7d8e 55%,#2d3d52)"></div>
  <div class="photo" role="img" aria-label="Outdoor condenser units beside a building" style="left:244px;top:1038px;width:300px;height:182px;background:linear-gradient(150deg,#d9a665,#8c8f8a 50%,#3e4a55)"></div>
  <h2 class="slab abs" style="left:603px;top:830px;font-size:39px;font-weight:600;color:var(--navy-deep)">Who We Are</h2>
  <p class="para" style="left:603px;top:889px;width:452px">Sed ut perspiciatis unde omnis iste natus error sit voluptatem accusantium doloremque laudantium, totam rem aperiam, eaque ipsa quae ab illo inventore veritatis et quasi architecto beatae vitae dicta sunt explicabo. Nemo enim ipsam voluptatem quia voluptas sit aspernatur aut odit aut fugit, sed quia consequuntur magni dolores eos qui ratione voluptatem sequi nesciunt. Neque porro quisquam est, qui dolorem ipsum quia dolorSed ut perspiciatis unde omnis iste natus error sit voluptatem accusantium doloremque laudantium, totam rem aperiam, eaque ipsa quae ab illo inventore veritatis et quasi architecto beatae vitae dicta sunt explicabo. Nemo enim ipsam voluptatem quia voluptas</p>
  <div class="btn" style="left:601px;top:1160px;width:134px;height:42px">Read more</div>
  <div class="abs" role="img" aria-label="White company service van with blue branding" style="left:795px;top:1192px;width:395px;height:142px;border-radius:40px 70px 24px 24px;background:linear-gradient(180deg,#f4f6f9,#d5dbe3 70%,#2a2f36)"></div>

  <!-- SERVICES -->
  <svg class="abs" style="left:0;top:1300px" width="1200" height="650" viewBox="0 1300 1200 650">
    <ellipse cx="600" cy="1620" rx="650" ry="320" fill="var(--grey)"/>
    <ellipse cx="600" cy="1620" rx="625" ry="298" fill="var(--navy)"/>
  </svg>
  <div class="ghost" style="top:1380px;color:rgba(255,255,255,.08)">Services</div>
  <div class="h2" style="top:1388px;color:var(--white)">Services</div>
  <div class="arrow" style="left:175px;top:1556px"><svg width="18" height="18" viewBox="0 0 18 18"><path d="M11 3L5 9l6 6" fill="none" stroke="#fff" stroke-width="2.2"/></svg></div>
  <div class="arrow" style="left:979px;top:1556px"><svg width="18" height="18" viewBox="0 0 18 18"><path d="M7 3l6 6-6 6" fill="none" stroke="#fff" stroke-width="2.2"/></svg></div>
  <div class="svc" style="left:264px;top:1472px">
    <svg width="60" height="64" viewBox="0 0 60 64" fill="none" stroke="#fff" stroke-width="2.4"><rect x="10" y="22" width="20" height="34" rx="6"/><path d="M20 22V12h22v14h10"/><circle cx="42" cy="42" r="10"/><path d="M42 34c-4 5 4 7 0 14"/></svg>
    <span>Gas Fitting</span>
  </div>
  <div class="svc" style="left:497px;top:1472px">
    <svg width="60" height="64" viewBox="0 0 60 64" fill="none" stroke="#fff" stroke-width="2.4"><rect x="8" y="6" width="14" height="10"/><path d="M15 16v18h24"/><rect x="39" y="28" width="10" height="14"/><path d="M49 35h6M15 34v22"/><rect x="10" y="50" width="10" height="8"/></svg>
    <span>Pipe Fitting</span>
  </div>
  <svg class="abs" style="left:587px;top:1678px" width="28" height="16"><path d="M0 0h28L14 16z" fill="#fff"/></svg>
  <div class="svc" style="left:727px;top:1472px">
    <svg width="60" height="64" viewBox="0 0 60 64" fill="none" stroke="#fff" stroke-width="2.4"><circle cx="30" cy="32" r="24"/><circle cx="30" cy="32" r="12"/><path d="M30 14v6M30 44v6M12 32h6M42 32h6M22 24l22 18"/></svg>
    <span>New Installs</span>
  </div>
  <p class="abs" style="left:285px;top:1726px;width:630px;text-align:center;font-size:13px;line-height:23.5px;color:var(--white)">Sed ut perspiciatis unde omnis iste natus error sit voluptatem accusantium doloremque laudantium, totam rem aperiam, eaque ipsa quae ab illo inventore veritatis et quasi architecto beatae vitae dicta sunt explicabo. Nemo enim ipsam voluptatem quia voluptas sit aspernatur au</p>
  <div class="btn on-dark" style="left:493px;top:1824px;width:213px;height:42px">View more services</div>

  <!-- WHAT WE DO -->
  <div class="vertical" style="left:1114px;top:2322px">WHAT WE DO</div>
  <h2 class="slab abs" style="left:143px;top:2025px;font-size:39px;font-weight:600;color:var(--navy-deep)">What We Do</h2>
  <p class="para" style="left:144px;top:2086px;width:453px">Sed ut perspiciatis unde omnis iste natus error sit voluptatem accusantium doloremque laudantium, totam rem aperiam, eaque ipsa quae ab illo inventore veritatis et quasi architecto beatae vitae dicta sunt explicabo. Nemo enim ipsam voluptatem quia voluptas sit aspernatur aut odit aut fugit, sed quia consequuntur magni dolores eos qui ratione voluptatem sequi nesciunt. Neque porro quisquam est, qui dolorem ipsum quia dolorSed ut perspiciatis unde omnis iste natus error sit voluptatem accusantium doloremque laudantium, totam rem aperiam, eaque ipsa quae ab illo inventore veritatis et quasi architecto beatae vitae dicta sunt explicabo. Nemo enim ipsam voluptatem quia voluptas</p>
  <div class="btn" style="left:142px;top:2356px;width:133px;height:42px">Read more</div>
  <div class="photo" role="img" aria-label="Plumber kneeling at work on an outdoor pipe" style="left:626px;top:2100px;width:464px;height:264px;background:linear-gradient(150deg,#9aa7b4,#5f6b77 50%,#3b4450)"></div>
  <div class="photo" role="img" aria-label="Technician in a plaid shirt at work" style="left:644px;top:2010px;width:268px;height:172px;background:linear-gradient(150deg,#c9cfd6,#6a7a93 55%,#3d4b63)"></div>
  <div class="photo" role="img" aria-label="Close view of a work boot and PVC pipe in soil" style="left:762px;top:2250px;width:238px;height:164px;background:linear-gradient(150deg,#8c8f92,#4c535b 60%,#2d3136)"></div>

  <!-- AREAS WE SERVE -->
  <svg class="abs" style="left:0;top:2430px" width="1200" height="1045" viewBox="0 2430 1200 1045">
    <ellipse cx="600" cy="2770" rx="660" ry="330" fill="var(--navy)"/>
    <rect x="0" y="2770" width="1200" height="705" fill="var(--navy)"/>
    <ellipse cx="600" cy="2770" rx="620" ry="302" fill="var(--grey)"/>
  </svg>
  <div class="ghost" style="top:2542px;color:rgba(18,63,122,.08)">Areas We Serve</div>
  <div class="h2" style="top:2548px;color:var(--navy-deep)">Areas We Serve</div>
  <div class="area-photo" role="img" aria-label="Downtown tower under a blue sky" style="left:144px;background:linear-gradient(180deg,#5b8fd1,#a9c6e6 50%,#6d7784)"></div>
  <div class="area-photo" role="img" aria-label="City skyline above a green park" style="left:374px;background:linear-gradient(180deg,#9bbde6,#c7d3db 45%,#5d8a4c)"></div>
  <div class="area-photo" role="img" aria-label="Brick city buildings along a waterfront" style="left:604px;background:linear-gradient(180deg,#3e7bd0,#8eb3e4 40%,#a0563b 70%,#4f6f8f)"></div>
  <div class="area-photo" role="img" aria-label="Modern office tower on a plaza" style="left:835px;background:linear-gradient(180deg,#b9c9dc,#8698ab 55%,#b4b8bc)"></div>
  <div class="area-label" style="left:144px">Accusantium</div>
  <div class="area-label" style="left:374px">Duis aute</div>
  <div class="area-label" style="left:604px">Voluptate</div>
  <div class="area-label" style="left:835px">Equi nesciun</div>
  <div class="btn" style="left:493px;top:2960px;width:213px;height:42px;background:transparent">View more areas</div>

  <!-- TESTIMONIALS -->
  <div class="ghost" style="top:3163px;color:rgba(255,255,255,.07)">Testimonials</div>
  <div class="h2" style="top:3168px;color:var(--white)">What Our Client Says</div>
  <div class="abs" style="left:0;width:1200px;top:3240px;text-align:center;font:900 62px Georgia,serif;color:var(--white);font-style:italic;line-height:60px">“</div>
  <p class="abs" style="left:232px;top:3310px;width:736px;text-align:center;font:italic 13.5px/23.5px Roboto,Arial,sans-serif;color:var(--white)">Sed ut perspiciatis unde omnis iste natus error sit voluptatem accusantium doloremque laudantium, totam rem aperiam, eaque ipsa quae ab illo inventore veritatis et quasi architecto beatae vitae dicta sunt explicabo. Nemo enim ipsam voluptatem quia voluptas sit aspernatur aut odit aut fugit, sed qui</p>
  <div class="abs" style="left:495px;top:3402px;font:italic 700 13px Roboto,Arial,sans-serif;color:var(--white)">SAM ELLERY</div>
  <div class="abs" style="left:592px;top:3394px;font-size:24px;letter-spacing:2px;color:var(--gold)">★★★★★</div>
  <div class="arrow" style="left:145px;top:3322px"><svg width="18" height="18" viewBox="0 0 18 18"><path d="M11 3L5 9l6 6" fill="none" stroke="#fff" stroke-width="2.2"/></svg></div>
  <div class="arrow" style="left:1006px;top:3322px"><svg width="18" height="18" viewBox="0 0 18 18"><path d="M7 3l6 6-6 6" fill="none" stroke="#fff" stroke-width="2.2"/></svg></div>

  <!-- LATEST NEWS -->
  <div class="abs" style="left:0;top:3471px;width:1200px;height:690px;background:#fafbfc"></div>
  <div class="ghost" style="top:3550px;color:rgba(18,63,122,.1)">Latest News</div>
  <div class="h2" style="top:3558px;color:var(--navy-deep)">Latest News</div>
  <article class="card" style="left:144px">
    <div class="img" role="img" aria-label="Plumber tightening a sink pipe with a wrench" style="background:linear-gradient(160deg,#e1e4e8,#9aa1a9 60%,#b05a3c)"></div>
    <h3>Nemo enim ipsam voluptatem quiaxercitation ullamcla</h3>
    <p>Sed ut perspiciatis unde omnis iste natus error sit voluptatemaccusantium doloremque laudantium, otam rem aperiam, eaque ipsa quaeb illo inventore veritatis</p>
    <div class="meta">January 31,2024 &nbsp;|&nbsp; Comments</div>
  </article>
  <article class="card" style="left:453px">
    <div class="img" role="img" aria-label="Homeowner adjusting a wall thermostat" style="background:linear-gradient(160deg,#f2efe9,#c7b8a3 55%,#8d9db5)"></div>
    <h3>Sed ut perspiciatis unde omnis iste natus error</h3>
    <p>Sed ut perspiciatis unde omnis iste natus error sit voluptatemaccusantium doloremque laudantium, otam rem aperiam, eaque ipsa quaeb illo inventore veritatis</p>
    <div class="meta">January 31,2024 &nbsp;|&nbsp; Comments</div>
  </article>
  <article class="card" style="left:760px">
    <div class="img" role="img" aria-label="Outdoor heat pump unit against a wall" style="background:linear-gradient(160deg,#d5d8da,#eef0f1 50%,#8a8f86)"></div>
    <h3>Neque porro quisquam estqui dolorem ipsum quiad</h3>
    <p>Sed ut perspiciatis unde omnis iste natus error sit voluptatemaccusantium doloremque laudantium, otam rem aperiam, eaque ipsa quaeb illo inventore veritatis</p>
    <div class="meta">January 31,2024 &nbsp;|&nbsp; Comments</div>
  </article>

  <!-- REQUEST A QUOTE -->
  <div class="abs" role="img" aria-label="Faded background of a technician servicing an outdoor AC unit" style="left:0;top:4153px;width:1200px;height:720px;background:linear-gradient(100deg,#d3d8dc 0%,#eef0f2 35%,#f6f7f8 60%,#dfe6dd 100%)"></div>
  <div class="vertical" style="left:64px;top:4460px;color:rgba(18,63,122,.12)">CONTACT</div>
  <div class="h2" style="top:4250px;color:var(--navy-deep)">Request A Quote</div>
  <div class="abs" style="left:0;width:1200px;top:4314px;text-align:center;font-size:16px;color:#4b5563">Contact us via text or email</div>
  <div class="field" style="left:213px;top:4391px;width:380px">Enter Name *</div>
  <div class="field" style="left:605px;top:4391px;width:380px">Enter Email *</div>
  <div class="field" style="left:213px;top:4456px;width:380px">Enter Phone *</div>
  <div class="field" style="left:605px;top:4456px;width:380px">Address</div>
  <div class="field" style="left:213px;top:4519px;width:772px;height:94px">Message</div>
  <div class="btn" style="left:213px;top:4630px;width:166px;height:42px;font-size:11px;gap:8px">Upload picture
    <svg width="16" height="16" viewBox="0 0 16 16" fill="none" stroke="#123f7a" stroke-width="1.8"><path d="M8 11V2M4.5 5.5L8 2l3.5 3.5M2 10v4h12v-4"/></svg></div>
  <div class="abs" style="left:412px;top:4642px;font-size:14px;color:#374151">Join Our Mailing List
    <span class="radio" style="margin-left:22px"></span><span style="font-size:11px">YES</span>
    <span class="radio"></span><span style="font-size:11px">NO</span></div>
  <div class="btn" style="left:536px;top:4689px;width:128px;height:40px">Submit</div>

  <!-- FOOTER -->
  <svg class="abs" style="left:0;top:4830px" width="1200" height="542" viewBox="0 4830 1200 542">
    <rect x="0" y="4860" width="1200" height="512" fill="var(--black)"/>
    <ellipse cx="600" cy="4860" rx="720" ry="64" fill="#f2f3f4"/>
  </svg>
  <div class="brand" style="left:512px;top:4896px;color:var(--navy)"><i></i>Pelican HVAC</div>

  <div class="foot-h" style="left:171px">Contact us</div>
  <svg class="abs" style="left:172px;top:5070px" width="14" height="18" viewBox="0 0 14 18"><path d="M7 0a7 7 0 0 0-7 7c0 5 7 11 7 11s7-6 7-11a7 7 0 0 0-7-7z" fill="#fff"/><circle cx="7" cy="7" r="2.6" fill="#0b0b0c"/></svg>
  <div class="foot-t" style="left:208px;top:5064px;width:170px">123,ores eos qui ratione voluptatem sequi nesciunt</div>
  <svg class="abs" style="left:172px;top:5122px" width="16" height="16" viewBox="0 0 16 16"><path d="M3 1l3.5 3.5-1.6 2.2c1 2 2.5 3.5 4.5 4.5l2.2-1.6L15 13l-2.3 2.4C7 15 1 9 .6 3.3z" fill="#fff"/></svg>
  <div class="foot-t" style="left:208px;top:5118px">Phone:<br>603-555-0148</div>
  <svg class="abs" style="left:172px;top:5178px" width="18" height="13" viewBox="0 0 18 13"><rect width="18" height="13" rx="1.5" fill="#fff"/><path d="M1 1l8 6 8-6" fill="none" stroke="#0b0b0c" stroke-width="1.5"/></svg>
  <div class="foot-t" style="left:208px;top:5172px">Email:<br>info@pelicanhvac.example</div>

  <div class="foot-h" style="left:507px">Sign up for newsletter</div>
  <div class="foot-t" style="left:507px;top:5066px;width:290px;font-size:12px">excepteur sint occaecat cupidatat non proident, sunt in culpa</div>
  <div class="abs" style="left:507px;top:5140px;width:256px;height:42px;border:1.5px solid #fff;border-radius:30px;padding:12px 20px;font-size:12px;color:#fff">Enter email</div>
  <div class="abs" style="left:507px;top:5194px;width:256px;height:40px;border-radius:30px;background:#fff;display:flex;align-items:center;justify-content:center;font:700 13px Roboto,Arial,sans-serif;color:#0b0b0c;text-transform:uppercase">Subscribe</div>

  <div class="foot-h" style="left:912px">Quick links</div>
  <div class="abs quick" style="left:916px;top:5060px">
    <a>Home</a><a>Our Services</a><a>About Us</a><a>Why Use Broker</a><a>Blog</a><a>Contact Us</a>
  </div>

  <div class="abs" style="left:171px;top:5316px;font-size:11.5px;color:#e5e7eb">Copyright ©2024 Pelican HVAC | Accessibility Statement | Privacy Policy | Sitemap</div>
  <svg class="abs" style="left:936px;top:5314px" width="96" height="18" viewBox="0 0 96 18"><circle cx="7" cy="9" r="6" fill="#fff"/><circle cx="45" cy="9" r="6" fill="#fff"/><circle cx="83" cy="9" r="6" fill="#fff"/></svg>

</div>
</body>
</html>
```